KTR Photography Editing & Support Services for Real Estate

We require a double sided A4 flyer to promote our photography services to real estate agencies.
This particular service is targeted to rural areas where reliable, professional and highly skilled photographers are difficult to source. We teach the agent how to photograph, they upload files to a server and we take care of the rest (image editing, quality control and delivery). This will give the agents flexibility with when to shoot and eliminates the stress of managing a photographer / contractor. We offer a 1 day face to face training session and competitive packages for equipment start up.
We would like the flyer to look clean & very professional. The flyer should showcase samples of our work to highlight what can be achieved by using our services. We like the look of a black or dark background behind the text and feel that would look nice with our photographs provided. Otherwise open to your suggestions and ideas.
TEXT FOR FLYER:
Welcome to the KTR Real Estate Photography Editing and Support Service
• Take your real estate business to the next level by providing impressive real estate imagery that makes you stands out from the competition
• Omit the stress of trying to find a good photographer or managing an unreliable one and hence have more time to focus on other aspects of your business
• Showcase your listings with better quality and more impactful photographs than your competitors thereby increasing potential for a quick sale
• Great first impressions matter and you will achieve this by looking and feeling more professional. This will attract and retain more future clients.
HOW IT WORKS
• We understand that your time is valuable, so let us handle the editing and delivery of your images. You shoot, and we take care of the rest.
• Images are edited and delivered within 1 working day
INCLUSIONS:
• Full day face to face training (we come to you) and instructional handbook
• We will teach you everything you need to know about your equipment and how to take stunning real estate photographs
• Service turnaround within 1 working day
• Free HELP desk service Mon-Fri
• 12 month Exclusivity (rural towns only) for a limited time
INVESTMENT
• 99 per listing for us to manage images including editing, quality control and delivery (10 Images)
• Ask us about competitive packages for photography equipment if required
SUMMARY
The KTR Real Estate Photography Editing and Support Service is the perfect solution for busy real estate professionals who want to take their business to the next level. Our service is affordable, flexible, and designed to help you showcase your listings in the best possible light.
Contact us today to learn more about how we can help you.

```html
<!DOCTYPE html>
<html lang="en">
<head>
<meta charset="utf-8">
<title>KTR Real Estate Photography Editing and Support Service – Flyer</title>
<link rel="stylesheet" href="https://fonts.googleapis.com/css2?family=Bellefair&family=Poppins:wght@300;400;500;600;700&family=Oswald:wght@500&display=swap">
<style>
  :root{
    --bg:#efefef;
    --ink:#141414;
    --ink-soft:#1c1c1c;
    --white:#ffffff;
    --text:#e6e6e6;
    --gold:#c29a62;
    --gold-light:#e0c08c;
    --gold-dark:#8c6b3e;
    --sky:#4a7fb3;
    --dusk:#c9b08c;
    --lawn:#3d4a25;
    --wood:#6b4a2c;
  }
  *{box-sizing:border-box;margin:0;padding:0}
  html,body{width:783px;height:1200px;overflow:hidden;background:var(--bg)}
  body{font-family:"Poppins",sans-serif;color:var(--text);position:relative}

  .sheet{position:absolute;top:345px;width:360px;height:509px;background:var(--ink);overflow:hidden;box-shadow:0 4px 12px rgba(0,0,0,.25)}
  .sheet--front{left:20px}
  .sheet--back{left:403px}
  .abs{position:absolute}

  /* photo placeholders */
  .photo-hero{left:0;top:0;width:360px;height:290px;
    background:linear-gradient(180deg,#3f74ad 0%,#8fa9c0 22%,#c9b89a 34%,#3a3a40 48%,#2e3522 68%,var(--lawn) 78%,var(--ink) 100%)}
  .photo-interior{left:0;top:0;width:360px;height:200px;
    background:linear-gradient(180deg,#7a5535 0%,#5b3f27 30%,#2c4f78 48%,#3b3a3a 70%,var(--ink) 100%)}
  .thumb{border:1.5px solid var(--white);height:82px;width:96px;top:191px}
  .thumb--kitchen{left:23px;background:linear-gradient(160deg,#f2f2f0,#c9c4bb 60%,#8a8378)}
  .thumb--farmhouse{left:132px;background:linear-gradient(180deg,#8e94b8,#cfc6c0 45%,#8e7a63 75%,#e9e7e4)}
  .thumb--coast{left:241px;background:linear-gradient(180deg,#7e9ec8,#e4b9a8 45%,#3b6f8f 60%,#4c7c33)}
  .thumb--hall{left:31px;top:390px;width:77px;height:62px;background:linear-gradient(120deg,#6c5a46,#d9d6cf 50%,#a8a59c)}
  .portrait{left:244px;top:377px;width:116px;height:132px;
    background:radial-gradient(ellipse 40% 30% at 55% 25%,#9a7560,transparent 70%),linear-gradient(180deg,transparent 0%,#1d1d1d 45%,#111 100%)}

  /* frame */
  .frame{left:77px;top:18px;width:265px;height:264px;border:1px solid var(--gold);border-left:none}
  .frame::after{content:"";position:absolute;left:-77px;bottom:-1px;width:185px;height:1px;background:var(--ink);display:none}
  .frame-bottom-mask{left:77px;top:280px;width:110px;height:4px;background:transparent}
  .frame-dot{width:4px;height:4px;border-radius:50%;background:var(--gold);left:250px;top:280px}

  /* name mark */
  .name-mark{left:14px;top:48px;width:138px;text-align:center;font-weight:300;font-size:9.5px;letter-spacing:2.2px;color:#3a3a3a}
  .name-mark--back{left:248px;top:472px;width:100px;font-size:7px;letter-spacing:1.6px;color:#cfcfcf}

  /* headline */
  .welcome{left:28px;top:212px;font-size:11px;font-weight:300;color:var(--white)}
  .headline{left:27px;top:226px;font-family:"Bellefair",serif;font-size:23px;line-height:23px;color:var(--white);letter-spacing:-.2px;white-space:nowrap}
  .headline .accent{color:var(--gold)}

  /* bullets */
  .ticks{list-style:none}
  .ticks li{position:relative;padding-left:11px;font-size:5.9px;line-height:7.3px;color:var(--text);margin-bottom:6px}
  .ticks li svg{position:absolute;left:0;top:1px;width:6px;height:6px}
  .benefits-left{left:28px;top:304px;width:132px}
  .benefits-right{left:190px;top:304px;width:140px}

  .section-title{font-weight:700;font-size:11.5px;letter-spacing:.2px;color:var(--gold)}
  .how-title{left:117px;top:385px}
  .how-list{left:117px;top:403px;width:130px}
  .inclusions-title{left:21px;top:290px}
  .inclusions-list{left:21px;top:310px;width:145px}
  .inclusions-list li{margin-bottom:5px}
  .investment-title{left:198px;top:290px}

  .price{left:198px;top:306px;font-family:"Oswald",sans-serif;font-weight:500;font-size:44px;line-height:44px;color:var(--gold)}
  .price-label{left:240px;top:311px;font-size:14.5px;font-weight:400;color:var(--white)}
  .price-note{left:240px;top:331px;width:96px;font-size:5.6px;line-height:6.4px;color:var(--text)}

  .ask-box{left:198px;top:364px;width:136px;height:38px;border:1px solid #d8d8d8;border-radius:5px;display:flex;align-items:center;padding:0 8px;gap:6px}
  .ask-box .lead{font-weight:600;font-size:6.6px;line-height:8px;color:var(--gold)}
  .ask-box .rule{width:1px;height:20px;background:#d8d8d8}
  .ask-box .rest{font-size:6.8px;line-height:8px;color:var(--white)}

  .summary-box{left:23px;top:417px;width:312px;height:36px;border:1px solid #d8d8d8;border-radius:6px;display:flex;align-items:center;justify-content:center;text-align:center;padding:0 12px;font-size:5.3px;line-height:6.6px;color:var(--white)}

  /* contact band */
  .contact-band{height:22px;display:flex;align-items:center;gap:7px;padding-left:16px;font-weight:600;font-size:8.6px;color:var(--ink);
    background:linear-gradient(90deg,var(--gold-dark),var(--gold-light) 55%,var(--gold));
    clip-path:polygon(10px 0,100% 0,calc(100% - 8px) 100%,0 100%)}
  .contact-band--front{left:16px;top:468px;width:232px}
  .contact-band--back{left:0;top:469px;width:245px;clip-path:polygon(0 0,100% 0,calc(100% - 8px) 100%,0 100%);padding-left:16px}
  .contact-band span{display:inline-flex;align-items:center;gap:2px}
  .contact-band svg{width:7px;height:7px}
</style>
</head>
<body>

<!-- Front side -->
<section class="sheet sheet--front">
  <div class="abs photo-hero" role="img" aria-label="Dusk photograph of a dark weatherboard home with lit porch, garden beds and gravel path"></div>
  <div class="abs frame"></div>
  <div class="abs frame-dot"></div>
  <div class="abs name-mark">REED HALLOWAY</div>

  <p class="abs welcome">Welcome to the</p>
  <h1 class="abs headline"><span class="accent">KTR REAL ESTATE</span><br>PHOTOGRAPHY EDITING<br>AND SUPPORT SERVICE</h1>

  <ul class="abs ticks benefits-left">
    <li><svg viewBox="0 0 10 10"><circle cx="5" cy="5" r="5" fill="var(--gold)"/><path d="M2.8 5.2l1.5 1.5 3-3" stroke="#141414" stroke-width="1.3" fill="none"/></svg>Take your real estate business to the next level by providing impressive real estate imagery that makes you stands out from the competition</li>
    <li><svg viewBox="0 0 10 10"><circle cx="5" cy="5" r="5" fill="var(--gold)"/><path d="M2.8 5.2l1.5 1.5 3-3" stroke="#141414" stroke-width="1.3" fill="none"/></svg>Omit the stress of trying to find a good photographer or managing an unreliable one and hence have more time to focus on other aspects of your business</li>
  </ul>
  <ul class="abs ticks benefits-right">
    <li><svg viewBox="0 0 10 10"><circle cx="5" cy="5" r="5" fill="var(--gold)"/><path d="M2.8 5.2l1.5 1.5 3-3" stroke="#141414" stroke-width="1.3" fill="none"/></svg>Showcase your listings with better quality and more impactful photographs than your competitors thereby increasing potential for a quick sale</li>
    <li><svg viewBox="0 0 10 10"><circle cx="5" cy="5" r="5" fill="var(--gold)"/><path d="M2.8 5.2l1.5 1.5 3-3" stroke="#141414" stroke-width="1.3" fill="none"/></svg>Great first impressions matter and you will achieve this by looking and feeling more professional. This will attract and retain more future clients.</li>
  </ul>

  <div class="abs thumb thumb--hall" role="img" aria-label="Photograph of a bright hallway with framed pictures"></div>
  <h2 class="abs section-title how-title">HOW IT WORKS</h2>
  <ul class="abs ticks how-list">
    <li><svg viewBox="0 0 10 10"><circle cx="5" cy="5" r="5" fill="var(--gold)"/><path d="M2.8 5.2l1.5 1.5 3-3" stroke="#141414" stroke-width="1.3" fill="none"/></svg>We understand that your time is valuable, so let us handle the editing and delivery of your images. You shoot, and we take care of the rest.</li>
    <li><svg viewBox="0 0 10 10"><circle cx="5" cy="5" r="5" fill="var(--gold)"/><path d="M2.8 5.2l1.5 1.5 3-3" stroke="#141414" stroke-width="1.3" fill="none"/></svg>Images are edited and delivered within 1 working day</li>
  </ul>

  <div class="abs portrait" role="img" aria-label="Portrait of the photographer in a black t-shirt with arms crossed"></div>

  <div class="abs contact-band contact-band--front">
    <span><svg viewBox="0 0 10 10"><path d="M2 1l2 2-1 1.2c.6 1.3 1.5 2.2 2.8 2.8L7 6l2 2-1.2 1.3C4.5 9 1 5.5.8 2.2z" fill="#141414"/></svg>+61 400 555 019</span>
    <span><svg viewBox="0 0 10 10"><rect x=".5" y="2" width="9" height="6" fill="#141414"/><path d="M.5 2l4.5 3.5L9.5 2" stroke="#c29a62" stroke-width=".8" fill="none"/></svg>shoot@reedhalloway.com.au</span>
  </div>
</section>

<!-- Back side -->
<section class="sheet sheet--back">
  <div class="abs photo-interior" role="img" aria-label="Dusk photograph of a timber-lined living room with hanging fireplace and tall glass windows"></div>
  <div class="abs thumb thumb--kitchen" role="img" aria-label="Photograph of a white kitchen and dining area"></div>
  <div class="abs thumb thumb--farmhouse" role="img" aria-label="Photograph of a stone and white farmhouse at dusk"></div>
  <div class="abs thumb thumb--coast" role="img" aria-label="Photograph of a dark cabin on a coastal cliff at sunset"></div>

  <h2 class="abs section-title inclusions-title">INCLUSIONS</h2>
  <ul class="abs ticks inclusions-list">
    <li><svg viewBox="0 0 10 10"><circle cx="5" cy="5" r="5" fill="var(--gold)"/><path d="M2.8 5.2l1.5 1.5 3-3" stroke="#141414" stroke-width="1.3" fill="none"/></svg>Full day face to face training (we come to you) and instructional handbook</li>
    <li><svg viewBox="0 0 10 10"><circle cx="5" cy="5" r="5" fill="var(--gold)"/><path d="M2.8 5.2l1.5 1.5 3-3" stroke="#141414" stroke-width="1.3" fill="none"/></svg>We will teach you everything you need to know about your equipment and how to take stunning real estate photographs</li>
    <li><svg viewBox="0 0 10 10"><circle cx="5" cy="5" r="5" fill="var(--gold)"/><path d="M2.8 5.2l1.5 1.5 3-3" stroke="#141414" stroke-width="1.3" fill="none"/></svg>Service turnaround within 1 working day</li>
    <li><svg viewBox="0 0 10 10"><circle cx="5" cy="5" r="5" fill="var(--gold)"/><path d="M2.8 5.2l1.5 1.5 3-3" stroke="#141414" stroke-width="1.3" fill="none"/></svg>Free HELP desk service Mon-Fri</li>
    <li><svg viewBox="0 0 10 10"><circle cx="5" cy="5" r="5" fill="var(--gold)"/><path d="M2.8 5.2l1.5 1.5 3-3" stroke="#141414" stroke-width="1.3" fill="none"/></svg>12 month Exclusivity (rural towns only) for a limited time</li>
  </ul>

  <h2 class="abs section-title investment-title">INVESTMENT</h2>
  <div class="abs price">99</div>
  <div class="abs price-label">per listing</div>
  <p class="abs price-note">for us to manage images including editing, quality control and delivery</p>

  <div class="abs ask-box">
    <span class="lead">ASK US ABOUT<br>COMPETITIVE<br>PACKAGES</span>
    <span class="rule"></span>
    <span class="rest">for photography<br>equipment if<br>required</span>
  </div>

  <p class="abs summary-box">The KTR Real Estate Photography Editing and Support Service is the perfect solution for busy real estate professionals who want to take their business to the next level. Our service is affordable, flexible, and designed to help you showcase your listings in the best possible light.</p>

  <div class="abs contact-band contact-band--back">
    <span><svg viewBox="0 0 10 10"><path d="M2 1l2 2-1 1.2c.6 1.3 1.5 2.2 2.8 2.8L7 6l2 2-1.2 1.3C4.5 9 1 5.5.8 2.2z" fill="#141414"/></svg>+61 400 555 019</span>
    <span><svg viewBox="0 0 10 10"><rect x=".5" y="2" width="9" height="6" fill="#141414"/><path d="M.5 2l4.5 3.5L9.5 2" stroke="#c29a62" stroke-width=".8" fill="none"/></svg>shoot@reedhalloway.com.au</span>
  </div>
  <div class="abs name-mark name-mark--back">REED HALLOWAY</div>
</section>

</body>
</html>
```